Design logo, business cards, and web page for new web and bi development consulting company

I've started a Web and Business Intelligence development consulting company. We develop on Quordex's stack, Vistral Studio and Quordex Data Server. We develop responsive web sites and business intelligence platforms. I plan on focusing on small to medium sized business as my client base. I need a logo, business cards, and a one page web site. We will do more with the web site with you in the next six months if the business survives. The name of the company is Corvalo Integration Solutions, Corvalo for short.

Target Market(s)

small to medium sized businesses

Industry/Entity Type

Business

Contact Information for Business Card

logo
name
title
email
phone

Logo Text

Corvalo Integration Solutions - web and data solutions

Coding

Coded - Design and coding required

Number of Pages Required

1 page

Font styles to use
Sans Serif

Colors
0355a3
0092cd
00a88f
6b449b

Requirements
Nice to have
• web and data solutions

```html
<!DOCTYPE html>
<html lang="en">
<head>
<meta charset="utf-8">
<title>Corvalo Integration Solutions</title>
<link href="https://fonts.googleapis.com/css2?family=Open+Sans:wght@400;600;700&family=Tenor+Sans&family=Ubuntu:wght@400;500&display=swap" rel="stylesheet">
<style>
  :root {
    --hero-dark: #14252b;
    --hero-mid: #1f3c44;
    --blue: #0092cd;
    --blue-deep: #0355a3;
    --blue-btn: #1a82c8;
    --teal: #1b7a6c;
    --teal-text: #1d5f56;
    --ink: #222;
    --body: #333;
    --rule: #b5b5b5;
    --strip: #e4e4e4;
    --footer: #4a4a4a;
    --footer-text: #f0f0f0;
  }
  * { box-sizing: border-box; margin: 0; padding: 0; }
  html, body { width: 954px; height: 1200px; overflow: hidden; }
  body { font-family: "Open Sans", sans-serif; color: var(--body); background: #fff; position: relative; }
  .abs { position: absolute; }

  /* Hero */
  .hero { left: 0; top: 0; width: 954px; height: 354px;
    background: radial-gradient(ellipse at 70% 35%, #2a4c55 0%, var(--hero-mid) 40%, var(--hero-dark) 100%); }
  .hero-floor { left: 0; top: 308px; width: 954px; height: 46px; background: rgba(0,0,0,0.12); }
  .brand { left: 78px; top: 32px; display: flex; align-items: flex-start; gap: 8px; }
  .brand-square { width: 18px; height: 14px; background: var(--blue); margin-top: 3px; }
  .brand-name { font-family: "Open Sans", sans-serif; font-weight: 700; font-size: 19px; color: #fff; line-height: 20px; letter-spacing: 0.5px; }
  .brand-tag { font-size: 8.5px; color: var(--blue); line-height: 10px; }
  .nav { left: 264px; top: 36px; display: flex; gap: 0; font-family: "Ubuntu", sans-serif; font-size: 11.5px; color: #fff; }
  .nav a { color: #fff; text-decoration: none; height: 25px; line-height: 25px; padding: 0 10px; margin-right: 17px; border-radius: 9px; }
  .nav a.active { background: var(--blue-btn); }
  .nav-line { left: 264px; top: 65px; width: 612px; height: 1px; background: rgba(255,255,255,0.1); }
  .hero-shot { left: 154px; top: 86px; width: 272px; height: 268px;
    background: linear-gradient(180deg, #1e64c8 0%, #2a7ae0 45%, #e9f1fa 46%, #f4f8fc 88%, #1f5cb8 100%); }
  .hero-title { left: 478px; top: 138px; font-family: "Tenor Sans", sans-serif; font-size: 29px; line-height: 36px; color: #fff; letter-spacing: 0.5px; }
  .hero-title span { color: #2a8ee8; }
  .hero-text { left: 478px; top: 220px; width: 350px; font-size: 9.4px; line-height: 16.5px; color: #d7e2e5; }
  .hero-btn { left: 478px; top: 289px; width: 149px; height: 26px; border-radius: 13px; background: var(--blue-btn);
    color: #fff; font-family: "Ubuntu", sans-serif; font-size: 11px; line-height: 26px; text-align: center; }

  .strip { left: 0; top: 354px; width: 954px; height: 34px; background: linear-gradient(#d9d9d9, #f2f2f2); }
  .dots { left: 152px; top: 367px; display: flex; gap: 8px; }
  .dots i { width: 11px; height: 11px; border-radius: 50%; background: #999; display: block; }
  .dots i.on { background: var(--blue-btn); }

  /* Welcome */
  .center { left: 0; width: 954px; text-align: center; }
  .h2 { font-family: "Tenor Sans", sans-serif; font-size: 17px; color: var(--ink); }
  .welcome-title { top: 400px; }
  .welcome-sub { top: 422px; font-family: "Tenor Sans", sans-serif; font-size: 11px; color: var(--teal-text); }
  .welcome-text { left: 180px; top: 441px; width: 594px; text-align: center; font-size: 8.6px; line-height: 16.5px; }
  .more-btn { left: 441px; top: 503px; width: 80px; height: 19px; border-radius: 10px; background: var(--blue-btn);
    color: #fff; font-family: "Ubuntu", sans-serif; font-size: 10px; line-height: 19px; text-align: center; }
  .rule { left: 143px; width: 669px; height: 1px; background: var(--rule); }
  .develop-title { top: 555px; }

  /* Cards */
  .card { top: 590px; width: 252px; }
  .card-head { height: 31px; background: var(--teal); color: #fff; font-family: "Tenor Sans", sans-serif; font-size: 15.5px; line-height: 31px; text-align: center; }
  .card-img { height: 121px; }
  .card-text { margin-top: 14px; text-align: center; font-size: 8.6px; line-height: 16.5px; }
  .read-more { display: block; margin-top: 6px; text-align: center; font-size: 9px; font-weight: 700; color: var(--teal-text); text-decoration: underline; letter-spacing: 0.3px; }

  /* About / works */
  .sec-title { font-family: "Tenor Sans", sans-serif; font-size: 16px; color: var(--ink); }
  .about-sub { left: 78px; top: 885px; font-family: "Tenor Sans", sans-serif; font-size: 11px; color: var(--teal-text); }
  .about-img { left: 78px; top: 913px; width: 173px; height: 121px; background: linear-gradient(135deg, #c9a27a, #3d5674 50%, #b7c4cf); }
  .about-text { left: 274px; top: 919px; width: 190px; font-size: 8.6px; line-height: 16.5px; }
  .continue { left: 274px; top: 1020px; font-size: 9px; font-weight: 700; color: var(--teal-text); text-decoration: underline; letter-spacing: 0.3px; }
  .work { top: 891px; width: 112px; height: 123px; border: 3px solid #fff; box-shadow: 0 0 3px rgba(0,0,0,0.45); }
  .arrow { top: 1023px; width: 10px; height: 10px; border-radius: 50%; }

  /* Footer */
  .footer { left: 0; top: 1068px; width: 954px; height: 132px; background: var(--footer); color: var(--footer-text); }
  .f-head { font-size: 10.5px; text-decoration: underline; color: #fff; }
  .f-list { list-style: none; font-size: 8px; line-height: 13.6px; margin-top: 6px; }
  .news-text { width: 240px; font-size: 8px; line-height: 13.6px; margin-top: 6px; }
  .email { left: 641px; top: 1142px; width: 163px; height: 24px; background: #fff; color: #555; font-size: 8px; line-height: 24px; padding-left: 12px; }
  .subscribe { left: 813px; top: 1142px; width: 62px; height: 24px; background: var(--blue-btn); color: #fff; font-size: 10px; line-height: 24px; text-align: center; }
</style>
</head>
<body>
  <header class="hero abs"></header>
  <div class="hero-floor abs"></div>
  <div class="brand abs">
    <div class="brand-square"></div>
    <div>
      <div class="brand-name">CORVALO</div>
      <div class="brand-tag">Integration solutions</div>
    </div>
  </div>
  <nav class="nav abs">
    <a class="active">HOME</a><a>DESIGN</a><a>DEVELOPMENT</a><a>WORKS</a><a>TEAM</a><a>CONTACT</a>
  </nav>
  <div class="nav-line abs"></div>
  <div class="hero-shot abs" role="img" aria-label="Website mockup showing a desktop computer and a special offer layout"></div>
  <h1 class="hero-title abs" style="font-weight:400">Professional Website<br><span>Developing</span></h1>
  <p class="hero-text abs">Lorem ipsum dolor sit amet, consec tetuer adipiscing elit. Prae sent vestibulum molestie lacus. Aenean nonummy hendrerit mauris. Pha sellus porta. Fusce suscipit varius mi.</p>
  <div class="hero-btn abs">WATCH OUR PORTFOLIO</div>

  <div class="strip abs"></div>
  <div class="dots abs"><i class="on"></i><i></i><i></i><i></i></div>

  <h2 class="h2 center abs welcome-title" style="font-weight:400">Welcome !</h2>
  <p class="welcome-sub center abs">We are a Web and Business Intelligence development consulting company.</p>
  <p class="welcome-text abs">Ut enim ad minim veniam, quis nostrud exercitation ullamco laboris nisi ut aliquip ex ea commodo consequat. Duis aute irure dolor in reprehenderit in voluptate velit esse cillum dolore eu fugiat nulla pariatur. Lorem ipsum dolor sit amet, consectetur adipisicing elit, sed do eiusmod tempor incidid-unt ut labore et dolore magna aliqua.</p>
  <div class="more-btn abs">MORE</div>
  <div class="rule abs" style="top:541px"></div>
  <h2 class="h2 center abs develop-title" style="font-weight:400">We develop on</h2>

  <section class="card abs" style="left:78px">
    <div class="card-head">Quordex's stack</div>
    <div class="card-img" role="img" aria-label="Monitor on a desk with notes and coffee" style="background:linear-gradient(135deg,#c29a70,#3f5877 50%,#a9b9c6)"></div>
    <p class="card-text">Lorem ipsum dolor sit amet, consec tetuer adipiscing elit. Praesent vestibulum molestie lacus. Aenean nonummy hendrerit mauris. Phasellus porta. Fusce suscipit varius mi.</p>
    <a class="read-more">READ MORE</a>
  </section>
  <section class="card abs" style="left:351px">
    <div class="card-head">Vistral Studio</div>
    <div class="card-img" role="img" aria-label="Responsive design shown on desktop, laptop, tablet and phone" style="background:linear-gradient(180deg,#e4e7ea,#4b4f55 50%,#d7dadd)"></div>
    <p class="card-text">Lorem ipsum dolor sit amet, consec tetuer adipiscing elit. Praesent vestibulum molestie lacus. Aenean nonummy hendrerit mauris. Phasellus porta. Fusce suscipit varius mi.</p>
    <a class="read-more">READ MORE</a>
  </section>
  <section class="card abs" style="left:624px">
    <div class="card-head">Quordex Data Server</div>
    <div class="card-img" role="img" aria-label="Developer pointing at floating website screens" style="background:linear-gradient(90deg,#5e8fc4,#e9edf2 45%,#3f63a8 75%,#d5dbe3)"></div>
    <p class="card-text">Lorem ipsum dolor sit amet, consec tetuer adipiscing elit. Praesent vestibulum molestie lacus. Aenean nonummy hendrerit mauris. Phasellus porta. Fusce suscipit varius mi.</p>
    <a class="read-more">READ MORE</a>
  </section>

  <div class="rule abs" style="top:842px"></div>

  <h2 class="sec-title abs" style="left:78px;top:861px;font-weight:400">About us</h2>
  <p class="about-sub abs">We also develop responsive web sites and business intelligence platforms</p>
  <div class="about-img abs" role="img" aria-label="Monitor on a desk with notes and coffee"></div>
  <p class="about-text abs">Lorem ipsum dolor sit amet, consec tetuer adipiscing elit. Praesent vestibulum molestie lacus. Aenean nounmy hendrerit mauris. Phasellus porta. Fusce suscipit varius mi. Lorem ipsum dolor sit amet, lacus...</p>
  <a class="continue abs">CONTINUE READING</a>

  <h2 class="sec-title abs" style="left:498px;top:861px;font-weight:400">Recent works</h2>
  <div class="work abs" style="left:498px;background:linear-gradient(180deg,#eee 15%,#c8452a 25%,#7b3c8f 45%,#ccc 60%,#999)" role="img" aria-label="Company website project preview"></div>
  <div class="work abs" style="left:631px;background:linear-gradient(180deg,#2b2b2b 55%,#e6e6e6 56%,#d0d0d0)" role="img" aria-label="Personal website project preview"></div>
  <div class="work abs" style="left:764px;background:linear-gradient(180deg,#3a2a1c 10%,#e98a1c 30%,#c9691a 55%,#3a2a1c 75%)" role="img" aria-label="Sample website project preview"></div>
  <svg class="arrow abs" style="left:854px" viewBox="0 0 10 10"><circle cx="5" cy="5" r="5" fill="#777"/><path d="M6 2.5 3.5 5 6 7.5" stroke="#fff" stroke-width="1.4" fill="none"/></svg>
  <svg class="arrow abs" style="left:866px" viewBox="0 0 10 10"><circle cx="5" cy="5" r="5" fill="#1a82c8"/><path d="M4 2.5 6.5 5 4 7.5" stroke="#fff" stroke-width="1.4" fill="none"/></svg>

  <footer class="footer abs">
    <div class="abs" style="left:78px;top:23px">
      <div class="f-head">Social Networks</div>
      <ul class="f-list"><li>Chirpline</li><li>Facepage</li><li>Snapgrid</li><li>Postwell</li></ul>
    </div>
    <div class="abs" style="left:310px;top:23px">
      <div class="f-head">Quick Solutions</div>
      <ul class="f-list"><li>Management Consulting</li><li>Policy and Regulatory Analysis</li><li>Market Assessment</li><li>Program Management</li></ul>
    </div>
    <div class="abs" style="left:439px;top:23px">
      <div class="f-head" style="visibility:hidden">.</div>
      <ul class="f-list"><li>Regulatory Support</li><li>Risk Assessment</li><li>Change Management</li><li>Information Technology</li></ul>
    </div>
    <div class="abs" style="left:641px;top:23px">
      <div class="f-head">Newsletter</div>
      <p class="news-text">Lorem ipsum dolor sit amet, consectetur adipiscing elit. Nulla vestibulum tincidunt justo, nec dapibus</p>
    </div>
  </footer>
  <div class="email abs">Email Address.....</div>
  <div class="subscribe abs">Subscribe</div>
</body>
</html>
```